Volbrey Inc Business Card

Looking to get an updated business card for a Contract Machining company (www.volbreyinc.example) - looking for a clean design the portrays the technical nature of the business - colors can follow the website design and be in any combination that makes sense (red black, white, metallic or silver) - logos attached for use also. Would like space for: Name, title, business phone (555 214-3086), cell phone , website (www.volbreyinc.example) - possibly QR code could be integrated for website (designer choice), business address - 418 Harlow Bend, Ashbury Falls, OR 97199 (cards will be for 4 employees, I will either need to modify a template or I can provide individual information)
Target Market(s)
Aerospace, defense and medical device manufacturing companies that need machining
Industry/Entity Type
Machining for aerospace, defense, medical
Contact Information for Business Card
Name, Title, Business Phone, Cell Phone, email, business website and business address
Look and feel

```html
<!DOCTYPE html>
<html lang="en">
<head>
<meta charset="utf-8">
<title>Volbrey Inc Business Card</title>
<link href="https://fonts.googleapis.com/css2?family=Montserrat:wght@400;700&display=swap" rel="stylesheet">
<style>
  :root {
    --card-black: #1b1b1c;
    --pattern-black: #161617;
    --brand-red: #b3333a;
    --text-white: #f2f2f2;
    --stage: #e9e8e6;
  }
  * { margin: 0; padding: 0; box-sizing: border-box; }
  html, body { width: 1200px; height: 780px; overflow: hidden; }
  body {
    background: var(--stage);
    font-family: "Montserrat", sans-serif;
    display: flex;
    align-items: center;
    justify-content: center;
    gap: 40px;
  }
  .card {
    position: relative;
    width: 540px;
    height: 309px;
    background: var(--card-black);
    box-shadow: 0 6px 18px rgba(0,0,0,0.18);
    overflow: hidden;
  }
  /* front */
  .brand {
    position: absolute;
    left: 172px;
    top: 34px;
    width: 110px;
    display: flex;
    flex-direction: column;
    align-items: center;
  }
  .brand-circle {
    width: 86px; height: 86px;
    border-radius: 50%;
    background: var(--brand-red);
  }
  .brand-name {
    margin-top: 8px;
    color: var(--brand-red);
    font-weight: 700;
    font-size: 19px;
    letter-spacing: 1px;
  }
  .person {
    position: absolute;
    right: 282px;
    top: 170px;
    text-align: right;
  }
  .person-name {
    color: var(--brand-red);
    font-weight: 700;
    font-size: 20px;
    letter-spacing: 1.5px;
    white-space: nowrap;
  }
  .person-title {
    color: var(--text-white);
    font-size: 14px;
    margin-top: 4px;
  }
  .divider {
    position: absolute;
    left: 270px;
    top: 160px;
    width: 1px;
    height: 66px;
    background: var(--brand-red);
  }
  .contacts {
    position: absolute;
    left: 284px;
    top: 160px;
    list-style: none;
    color: var(--text-white);
    font-size: 13px;
    line-height: 22px;
  }
  .contacts li { display: flex; align-items: center; gap: 8px; white-space: nowrap; }
  .contacts svg { width: 13px; height: 13px; flex: none; }
  .address-band {
    position: absolute;
    left: 0; right: 0;
    top: 243px;
    height: 24px;
    background: var(--brand-red);
    color: var(--text-white);
    font-size: 13px;
    line-height: 24px;
    padding-left: 130px;
    white-space: nowrap;
  }
  /* back */
  .back-pattern {
    position: absolute;
    inset: 0;
    background: var(--pattern-black);
  }
  .back-mark {
    position: absolute;
    left: 360px;
    top: 186px;
    display: flex;
    align-items: center;
    gap: 8px;
  }
  .back-circle {
    width: 60px; height: 60px;
    border-radius: 50%;
    background: var(--brand-red);
  }
  .back-name {
    color: var(--brand-red);
    font-weight: 700;
    font-size: 14px;
    letter-spacing: 1px;
  }
</style>
</head>
<body>
  <section class="card card-front">
    <div class="brand">
      <div class="brand-circle"></div>
      <div class="brand-name">VOLBREY</div>
    </div>

    <div class="person">
      <div class="person-name">DANIEL HARWICK</div>
      <div class="person-title">Managing Director</div>
    </div>

    <div class="divider"></div>

    <ul class="contacts">
      <li>
        <svg viewBox="0 0 16 16" aria-hidden="true"><path fill="#b3333a" d="M3.6 1.5l2.3 2.3-1.3 1.9c.9 2 2.6 3.6 4.6 4.6l1.9-1.3 2.3 2.3-1.6 2.2C6.9 13.3 2.7 9.1 1.4 3.2z"/></svg>
        (555 214-3086)
      </li>
      <li>
        <svg viewBox="0 0 16 16" aria-hidden="true"><rect x="4" y="1" width="8" height="14" rx="1.5" fill="none" stroke="#b3333a" stroke-width="1.5"/><circle cx="8" cy="12.5" r="0.9" fill="#b3333a"/></svg>
        (555 214-3086)
      </li>
      <li>
        <svg viewBox="0 0 16 16" aria-hidden="true"><circle cx="8" cy="8" r="6.5" fill="none" stroke="#b3333a" stroke-width="1.5"/><ellipse cx="8" cy="8" rx="2.8" ry="6.5" fill="none" stroke="#b3333a" stroke-width="1.2"/><line x1="1.5" y1="8" x2="14.5" y2="8" stroke="#b3333a" stroke-width="1.2"/></svg>
        www.volbreyinc.example
      </li>
    </ul>

    <div class="address-band">418 Harlow Bend, Ashbury Falls, OR 97199</div>
  </section>

  <section class="card card-back">
    <div class="back-pattern" role="img" aria-label="Tonal embossed pattern of repeated brand marks on black"></div>
    <div class="back-mark">
      <div class="back-circle"></div>
      <div class="back-name">VOLBREY</div>
    </div>
  </section>
</body>
</html>
```